Wesbite design for Investment Firm

We want a basic (clean) website that follows the form, fonts and colors of our attachments. This is for a financial investment management firm, but we have a boutique (anti-Wall Street) approach. Site should have an Home Page (Logo up top - room for basic copy on bottom, Philosophy Page (room for Quarterly Letter attachment and basic copy, Performance Page (room for Performance Overview and Performance Analysis and basic copy), Team Page, Commentary Page and Contact

Reason: Some designers have asked for an extension. Again, please only use image of Train Station or Train Station Logo in design.

Target Market(s)

Small and mid-size financial advisors from across the country

Industry/Entity Type

Financial

Number of Pages Required

5+ page

Font styles to use
Other font styles liked:
• Palotino Linotype

Colors
3176b5
cfdeed
ffffff

Requirements
Must have
• Please refer to existing site www.qlvor.example. Of note, this is too complex / cluttered. We simply want Blur, Grey and White consistent with attachments. The copy is pretty good, but will be simplified (and no quotes)
Should not have
• No images other than train station logo and / or train station image

```html
<!DOCTYPE html>
<html lang="en">
<head>
<meta charset="utf-8">
<title>Linden Hill Investment Company</title>
<link href="https://fonts.googleapis.com/css2?family=Lato:wght@300;400;700&family=Montserrat:wght@400;600;700&display=swap" rel="stylesheet">
<style>
:root{
  --blue:#3176b5;
  --blue-pale:#cfdeed;
  --navy:#1d4a86;
  --navy-dark:#163a6d;
  --white:#ffffff;
  --grey-bg:#f2f3f5;
  --grey-text:#6b6f75;
  --ink:#2d3136;
  --footer:#eceef1;
}
*{box-sizing:border-box;margin:0;padding:0}
html,body{width:1200px;height:2788px;overflow:hidden}
body{font-family:"Lato",sans-serif;color:var(--ink);background:var(--white);position:relative}
.btn{display:inline-block;font-family:"Montserrat",sans-serif;font-size:13px;font-weight:600;letter-spacing:1px;text-transform:uppercase;padding:12px 24px;text-decoration:none}
.btn-solid{background:var(--blue);color:var(--white)}
.btn-outline{border:2px solid var(--blue);color:var(--blue);background:var(--white)}

/* header */
.site-header{height:168px;text-align:center;background:var(--white)}
.brand{padding-top:18px;font-family:"Lato",sans-serif;font-size:38px;font-weight:700;color:var(--navy)}
.tagline{font-size:17px;color:var(--blue);margin-top:4px}
.main-nav{position:absolute;top:120px;left:0;width:1200px;height:48px;background:linear-gradient(var(--navy),var(--navy-dark));display:flex;justify-content:center}
.main-nav a{color:var(--white);text-decoration:none;font-family:"Montserrat",sans-serif;font-size:17px;font-weight:600;padding:0 52px;line-height:48px}
.main-nav a.active{background:#0f2d58}

/* hero */
.hero{position:absolute;top:168px;left:0;width:1200px;height:552px}
.hero-photo{position:absolute;inset:0;background:linear-gradient(180deg,#8fa1b4 0%,#a9b1b7 35%,#6d7377 70%,#54585a 100%)}
.hero-title{position:absolute;left:22px;top:196px;color:var(--white);font-family:"Montserrat",sans-serif;font-weight:600;line-height:1.15}
.hero-title .l1{font-size:54px}
.hero-title .l2{font-size:38px}
.hero-dots{position:absolute;bottom:24px;left:0;width:100%;display:flex;justify-content:center;gap:10px}
.hero-dots span{width:36px;height:4px;background:rgba(255,255,255,.5)}
.hero-dots span.on{background:var(--white)}

/* intro */
.intro{position:absolute;top:720px;left:0;width:1200px;height:408px;background:var(--white)}
.intro-copy{position:absolute;left:120px;top:84px;width:440px}
.intro-copy h2{font-size:34px;font-weight:400;color:var(--ink);margin-bottom:14px}
.intro-copy p{font-size:13px;line-height:1.6;color:var(--grey-text);margin-bottom:14px}
.intro-photo{position:absolute;left:580px;top:0;width:620px;height:408px;background:linear-gradient(135deg,#eef2f6 0%,#c9d3dd 45%,#7c8794 100%)}

/* services */
.services{position:absolute;top:1128px;left:0;width:1200px;height:412px;background:linear-gradient(180deg,var(--blue-pale) 0%,#7fa8d2 50%,var(--blue) 100%)}
.service-card{position:absolute;top:96px;width:470px;height:262px;border:2px solid var(--white);text-align:center;color:var(--white);padding:0 36px}
.service-card.left{left:112px}
.service-card.right{left:618px}
.service-icon{position:absolute;top:-40px;left:50%;margin-left:-42px;width:84px;height:84px;border-radius:50%;background:var(--blue);border:3px solid var(--white);display:flex;align-items:center;justify-content:center}
.service-card h3{margin-top:70px;font-size:30px;font-weight:400}
.service-card p{font-size:12px;line-height:1.6;margin:14px 0 18px}
.service-card .btn{border:2px solid var(--white);color:var(--white);padding:8px 22px;font-size:11px}

/* team */
.team{position:absolute;top:1540px;left:0;width:1200px;height:460px;background:var(--grey-bg)}
.team h2{text-align:center;margin-top:70px;font-size:34px;font-weight:700;color:var(--ink)}
.team-grid{position:absolute;top:142px;left:130px;display:flex;gap:22px}
.member{position:relative;width:218px;height:244px;border:4px solid #1b1d20}
.member-photo{position:absolute;inset:0}
.member .caption{position:absolute;bottom:22px;width:100%;text-align:center;color:var(--white)}
.member .name{font-size:17px;font-weight:700}
.member .post{font-size:13px;opacity:.85}

/* letter & commentary */
.letter{position:absolute;top:2000px;left:0;width:600px;height:400px;background:linear-gradient(135deg,var(--blue) 0%,#5f97cb 60%,var(--blue-pale) 100%);color:var(--white)}
.letter-copy{position:absolute;left:120px;top:84px;width:240px}
.letter-copy h2{font-size:28px;font-weight:400;line-height:1.15;margin-bottom:14px}
.letter-copy p{font-size:11px;line-height:1.6;margin-bottom:22px}
.letter-copy .btn{background:var(--white);color:var(--blue);padding:8px 22px;font-size:11px}
.letter-doc{position:absolute;left:386px;top:84px;width:150px;height:220px;background:var(--white);box-shadow:0 6px 16px rgba(0,0,0,.2)}
.commentary{position:absolute;top:2000px;left:600px;width:600px;height:400px;background:var(--white)}
.commentary-inner{position:absolute;left:60px;top:80px;width:420px}
.commentary h2{font-size:34px;font-weight:400;margin-bottom:16px}
.commentary h4{font-size:15px;color:var(--navy);font-weight:700}
.commentary .date{font-size:11px;color:var(--grey-text);margin:8px 0}
.commentary p{font-size:12px;line-height:1.6;color:var(--grey-text);margin-bottom:18px}
.commentary .btn{padding:8px 22px;font-size:11px}

/* footer */
.site-footer{position:absolute;top:2400px;left:0;width:1200px;height:320px;background:var(--footer)}
.foot-col{position:absolute;top:62px}
.foot-col h5{font-family:"Montserrat",sans-serif;font-size:15px;font-weight:600;color:var(--blue);margin-bottom:14px;letter-spacing:.5px}
.foot-col ul{list-style:none}
.foot-col li{font-size:13px;line-height:1.75;color:var(--grey-text)}
.contact-line{display:flex;gap:8px;align-items:flex-start}
.social{display:flex;gap:10px}
.social span{width:30px;height:30px;border-radius:50%;background:var(--navy)}
.copyright{position:absolute;top:2720px;left:0;width:1200px;height:68px;line-height:68px;text-align:center;font-size:13px;color:var(--grey-text);background:var(--white);border-top:1px solid #dde1e6}
</style>
</head>
<body>

<header class="site-header">
  <div class="brand">Linden Hill Investment Company</div>
  <div class="tagline">Separately Managed Accounts</div>
  <nav class="main-nav">
    <a class="active" href="#">Home</a>
    <a href="#">Philosophy</a>
    <a href="#">Performance</a>
    <a href="#">Team</a>
    <a href="#">Commentary</a>
    <a href="#">Contact</a>
  </nav>
</header>

<section class="hero">
  <div class="hero-photo" role="img" aria-label="Historic train station building under a pale sky"></div>
  <h1 class="hero-title"><span class="l1">FINANCIAL INVESTMENT</span><br><span class="l2">MANAGEMENT FIRM</span></h1>
  <div class="hero-dots"><span class="on"></span><span></span><span></span><span></span></div>
</section>

<section class="intro">
  <div class="intro-copy">
    <h2>Linden Hill Investment Company</h2>
    <p>We manage separate accounts for advisors with a patient, independent approach. Our small team keeps research close, costs low and every decision grounded in long term value for clients across the country.</p>
    <p>We invest as owners, not traders, and we write plainly about what we hold and why we hold it.</p>
    <a class="btn btn-solid" href="#">Learn More</a>
  </div>
  <div class="intro-photo" role="img" aria-label="Advisors shaking hands across a desk"></div>
</section>

<section class="services">
  <div class="service-card left">
    <div class="service-icon">
      <svg width="44" height="44" viewBox="0 0 44 44" fill="none" stroke="#fff" stroke-width="2.5"><circle cx="22" cy="22" r="15"/><path d="M22 10v24M12 22h20"/></svg>
    </div>
    <h3>Philosophy</h3>
    <p>Disciplined research, concentrated holdings and honest reporting guide each portfolio we build for advisors and their clients.</p>
    <a class="btn" href="#">Learn More</a>
  </div>
  <div class="service-card right">
    <div class="service-icon">
      <svg width="44" height="44" viewBox="0 0 44 44" fill="none" stroke="#fff" stroke-width="2.5"><circle cx="22" cy="22" r="15"/><path d="M22 22l8-8M22 22v-9"/></svg>
    </div>
    <h3>Performance</h3>
    <p>Review our performance overview and quarterly analysis to see how our strategies have fared through full market cycles.</p>
    <a class="btn" href="#">Learn More</a>
  </div>
</section>

<section class="team">
  <h2>Our Team</h2>
  <div class="team-grid">
    <div class="member"><div class="member-photo" role="img" aria-label="Portrait of a team member" style="background:linear-gradient(180deg,#5a5f66,#2f3338)"></div><div class="caption"><div class="name">Member Name</div><div class="post">Post Title</div></div></div>
    <div class="member"><div class="member-photo" role="img" aria-label="Portrait of a team member" style="background:linear-gradient(180deg,#6f9aa3,#3e5a60)"></div><div class="caption"><div class="name">Member Name</div><div class="post">Post Title</div></div></div>
    <div class="member"><div class="member-photo" role="img" aria-label="Portrait of a team member" style="background:linear-gradient(180deg,#d7d9dc,#8a8f95)"></div><div class="caption"><div class="name">Member Name</div><div class="post">Post Title</div></div></div>
    <div class="member"><div class="member-photo" role="img" aria-label="Portrait of a team member" style="background:linear-gradient(180deg,#4e6a8e,#233a58)"></div><div class="caption"><div class="name">Member Name</div><div class="post">Post Title</div></div></div>
  </div>
</section>

<section class="letter">
  <div class="letter-copy">
    <h2>Investment Adviser's Letter</h2>
    <p>Our quarterly letter shares portfolio updates, market notes and the thinking behind recent changes.</p>
    <a class="btn" href="#">Read More</a>
  </div>
  <div class="letter-doc" role="img" aria-label="Cover page of the quarterly letter"></div>
</section>

<section class="commentary">
  <div class="commentary-inner">
    <h2>Latest Commentary</h2>
    <h4>Core Equity Portfolio – Q2 2017</h4>
    <div class="date">AUGUST 10, 2017</div>
    <p>A short review of the quarter covering our largest holdings, new positions and the outlook for the months ahead.</p>
    <a class="btn btn-outline" href="#">Read More</a>
  </div>
</section>

<footer class="site-footer">
  <div class="foot-col" style="left:120px;width:230px">
    <h5>CONTACT US</h5>
    <ul>
      <li class="contact-line"><svg width="12" height="16" viewBox="0 0 12 16"><path d="M6 0a6 6 0 0 0-6 6c0 4.5 6 10 6 10s6-5.5 6-10a6 6 0 0 0-6-6zm0 8.5A2.5 2.5 0 1 1 6 3.5a2.5 2.5 0 0 1 0 5z" fill="#6b6f75"/></svg><span>820 Orchard Row,<br>Suite 210, Fairview, TX 75000</span></li>
      <li>555-014-2288</li>
      <li>hello@qlvor.example</li>
    </ul>
  </div>
  <div class="foot-col" style="left:430px">
    <h5>QUICK LINKS</h5>
    <ul><li>Home</li><li>Philosophy</li><li>Performance</li><li>Team</li><li>Commentary</li></ul>
  </div>
  <div class="foot-col" style="left:680px">
    <h5>RESOURCES</h5>
    <ul><li>Performance Overview</li><li>Performance Analysis</li><li>Quarterly Letters</li><li>Disclosures</li></ul>
  </div>
  <div class="foot-col" style="left:930px">
    <h5>GET IN TOUCH</h5>
    <div class="social"><span></span><span></span><span></span><span></span></div>
  </div>
</footer>
<div class="copyright">© 2017 Company Name. All rights reserved</div>

</body>
</html>
```